Business Card Design

WE are looking for a premium quality Business Cards for a Law Firm . Copies of our current business card is attached.

Contact Information for Business Card

xyz

```html
<!DOCTYPE html>
<html lang="en">
<head>
<meta charset="utf-8">
<title>Harlow Lawyers – Business Card</title>
<link href="https://fonts.googleapis.com/css2?family=Libre+Baskerville:wght@400;700&display=swap" rel="stylesheet">
<style>
  :root {
    --backdrop: #141417;
    --card: #1d1d22;
    --emboss: #0f0f13;
    --emboss-edge: #2a2a31;
    --gold: #c9a45c;
    --ink: #f4f2ee;
  }
  * { box-sizing: border-box; margin: 0; padding: 0; }
  html, body { width: 1200px; height: 780px; overflow: hidden; }
  body {
    background: var(--backdrop);
    font-family: "Libre Baskerville", "Times New Roman", serif;
    display: flex;
    align-items: center;
    justify-content: center;
    gap: 50px;
  }
  .card {
    position: relative;
    width: 540px;
    height: 310px;
    background: var(--card);
    border-left: 3px solid var(--gold);
    border-bottom: 3px solid var(--gold);
    overflow: hidden;
  }

  /* Front */
  .card-front {
    display: flex;
    flex-direction: column;
    align-items: center;
    justify-content: center;
    gap: 22px;
  }
  .front-seal {
    width: 96px;
    height: 96px;
    border-radius: 50%;
    border: 6px solid var(--emboss);
  }
  .front-name {
    font-weight: 700;
    font-size: 40px;
    letter-spacing: 1px;
    color: var(--emboss);
  }

  /* Back */
  .holder {
    position: absolute;
    top: 22px;
    right: 0;
    text-align: right;
    padding-right: 34px;
  }
  .holder::after {
    content: "";
    position: absolute;
    top: 0;
    right: 0;
    width: 16px;
    height: 56px;
    background: var(--gold);
  }
  .holder-name {
    font-weight: 700;
    font-size: 24px;
    color: var(--gold);
    line-height: 1.1;
  }
  .holder-role, .holder-degrees {
    font-weight: 700;
    font-size: 11px;
    color: var(--ink);
    line-height: 1.5;
  }
  .back-seal {
    position: absolute;
    right: 40px;
    bottom: 26px;
    width: 170px;
    height: 170px;
    border-radius: 50%;
    border: 8px solid var(--emboss);
    box-shadow: 0 0 0 1px var(--emboss-edge);
  }
  .firm {
    position: absolute;
    left: 30px;
    top: 104px;
    display: flex;
    align-items: center;
    gap: 10px;
  }
  .firm-mark {
    width: 30px;
    height: 30px;
    border-radius: 50%;
    border: 3px solid var(--gold);
  }
  .firm-name {
    font-weight: 700;
    font-size: 20px;
    color: var(--ink);
  }
  .address {
    position: absolute;
    left: 30px;
    top: 150px;
    font-style: normal;
    font-weight: 700;
    font-size: 12px;
    line-height: 1.45;
    color: var(--ink);
  }
  .contacts {
    position: absolute;
    left: 30px;
    top: 210px;
    list-style: none;
  }
  .contacts li {
    display: flex;
    align-items: center;
    gap: 8px;
    font-weight: 700;
    font-size: 12px;
    line-height: 19px;
    color: var(--ink);
  }
  .contacts svg { width: 12px; height: 12px; flex: none; }
</style>
</head>
<body>

  <section class="card card-front" aria-label="Card front">
    <div class="front-seal"></div>
    <div class="front-name">HARLOW LAWYERS</div>
  </section>

  <section class="card card-back" aria-label="Card back">
    <div class="holder">
      <div class="holder-name">DANIEL MERCER</div>
      <div class="holder-role">Director and Principal Solicitor</div>
      <div class="holder-degrees">MBA, Juris Doctor</div>
    </div>

    <div class="back-seal"></div>

    <div class="firm">
      <div class="firm-mark"></div>
      <div class="firm-name">HARLOW LAWYERS</div>
    </div>

    <address class="address">
      Level 3, Harlow House,<br>
      210 Ellison Terrace,<br>
      Northgate, QLD 4000
    </address>

    <ul class="contacts">
      <li>
        <svg viewBox="0 0 12 12"><path d="M2.5 1 L4.5 1 L5.2 3.6 L4 4.6 Q5 7 7.4 8 L8.4 6.8 L11 7.5 L11 9.5 Q11 11 9.5 11 Q1 10.4 1 2.5 Q1 1 2.5 1Z" fill="var(--gold)"/></svg>
        +61 7 3000 1234
      </li>
      <li>
        <svg viewBox="0 0 12 12"><rect x="3" y="0.8" width="6" height="10.4" rx="1" fill="none" stroke="var(--gold)" stroke-width="1.2"/><circle cx="6" cy="9.4" r="0.7" fill="var(--gold)"/></svg>
        +61 0400 555 010
      </li>
      <li>
        <svg viewBox="0 0 12 12"><circle cx="6" cy="6" r="5" fill="none" stroke="var(--gold)" stroke-width="1.2"/><ellipse cx="6" cy="6" rx="2.2" ry="5" fill="none" stroke="var(--gold)" stroke-width="1"/><line x1="1" y1="6" x2="11" y2="6" stroke="var(--gold)" stroke-width="1"/></svg>
        www.harlowlawyers.com.au
      </li>
      <li>
        <svg viewBox="0 0 12 12"><rect x="0.8" y="2.2" width="10.4" height="7.6" fill="none" stroke="var(--gold)" stroke-width="1.2"/><path d="M0.8 2.4 L6 6.6 L11.2 2.4" fill="none" stroke="var(--gold)" stroke-width="1.2"/></svg>
        daniel@harlowlawyers.com.au
      </li>
    </ul>
  </section>

</body>
</html>
```